Online Advice via Video Site requires Cutting Edge Homepage

We need a creative new and exciting webdesign for our tutoring via video-chat website.

We have prepared a "demo" homepage for you to see various promotional material that we think would be suitable for the homepage. http://www.quillmarsh.com/demo

The actual site is undergoing some final tinkering but can be accessed and used at http://www.quillmarsh.com

There is NO NEED to take any colours or design structure from this.

We expect the logo to be changed to match the new site. The new logo should match the site's function.

I have included some other projects that we like the look of:
http://www.vantoplex.com.au/design/143762
http://www.vantoplex.com.au/design/561630
http://www.vantoplex.com.au/design/247199
http://www.vantoplex.com.au/design/255195
http://www.birchlume.tv/

Target Market(s)

People that will work as tutors/advisers or be student/clients

Industry/Entity Type

Tutoring

Requirements
Must have
• The search is the main feature of the homepage

After the search the next goal of the page is to get people to sign up to the site

Login, (optional inclusion of the gablenet login - if you don't include it then you need only have a "login" button... no username or password input fields)

Footer
Nice to have
• The promotional material for the site, the colours on the Prezi file CAN BE changed to suit the new design you propose.

```html
<!DOCTYPE html>
<html lang="en">
<head>
<meta charset="utf-8">
<title>Quill Marsh – Online Advice</title>
<link href="https://fonts.googleapis.com/css2?family=PT+Sans:wght@400;700&family=Raleway:wght@300&family=Roboto+Condensed:wght@700&display=swap" rel="stylesheet">
<style>
:root{
  --page:#f0f0f0;
  --ink:#3a3a3a;
  --muted:#555;
  --logo:#2a4fa8;
  --bar-top:#f4f4f4;
  --bar-bottom:#d9d9d9;
  --line:#c8c8c8;
  --panel:#dcdcdc;
  --social:#3d3d3d;
  --gablenet:#3b5998;
  --footer:#333;
  --footer-text:#ddd;
}
*{margin:0;padding:0;box-sizing:border-box}
html,body{width:968px;height:1200px;overflow:hidden}
body{background:var(--page);font-family:"PT Sans",sans-serif;color:var(--ink);position:relative}
.abs{position:absolute}
.header{left:48px;top:0;width:874px;height:106px;background:linear-gradient(#f3f3f3,#fff 40%,#fafafa)}
.logo{left:75px;top:40px;font-family:"Raleway",sans-serif;font-weight:300;font-size:31px;color:var(--logo)}
.social-login{left:502px;top:40px;width:81px;height:20px;background:var(--gablenet);border:1px solid #2b4680;color:#fff;font-size:11px;font-weight:700;display:flex;align-items:center;gap:13px;padding-left:3px}
.social-login .box{width:14px;height:14px;background:#fff;opacity:.85}
.field{top:40px;height:22px;border:1px solid #bbb;background:#fff;font-style:italic;font-size:12px;color:#777;padding:4px 14px}
.btn-login{left:855px;top:40px;width:57px;height:23px;border-radius:6px;background:linear-gradient(#d8d6d0,#9d9a92);color:#fff;font-size:12px;font-weight:700;text-align:center;line-height:23px}
.remember{left:612px;top:72px;font-size:11px;color:#444;display:flex;align-items:center;gap:7px}
.remember span{width:11px;height:11px;border:1px solid #999;background:#fff}
.searchbar{left:48px;top:106px;width:874px;height:53px;background:linear-gradient(var(--bar-top),var(--bar-bottom));border:1px solid var(--line);border-bottom:none}
.pill{top:120px;height:25px;border:1px solid #aaa;border-radius:13px;background:linear-gradient(#fff,#ececec);font-style:italic;font-size:12px;color:#777;padding:4px 16px}
.pill.topics::after{content:"";position:absolute;right:10px;top:10px;border:4px solid transparent;border-top-color:#555}
.btn-search{left:390px;top:120px;width:106px;height:28px;border-radius:4px;background:linear-gradient(#c9c6bf,#8e8a82);color:#fff;font-family:"Roboto Condensed",sans-serif;font-size:13px;text-align:center;line-height:28px}
.adv{left:520px;top:126px;font-family:"Roboto Condensed",sans-serif;font-size:12px;color:#999}
.social{top:119px;width:28px;height:28px;border-radius:50%;background:var(--social);box-shadow:0 1px 2px rgba(0,0,0,.4)}
.hero{left:48px;top:159px;width:874px;height:346px;background:linear-gradient(90deg,#c9ced4 0%,#e6e8ea 25%,#8a7b70 45%,#b9a89a 55%,#d0d8e2 75%,#e9eef4 100%)}
.caption{left:48px;top:447px;width:874px;height:58px;background:rgba(200,200,200,.55);color:#fff;font-style:italic;font-weight:700;font-size:17.5px;line-height:56px;text-align:center}
.menu{left:48px;top:505px;width:874px;height:40px;background:linear-gradient(#f2f2f2,#d8d8d8);border:1px solid var(--line);font-family:"Roboto Condensed",sans-serif;font-size:12.5px;color:#333}
.menu a{position:absolute;top:12px;color:inherit;text-decoration:none}
.dots{right:14px;top:14px;display:flex;gap:4px}
.dots i{width:10px;height:10px;border-radius:50%;background:#eee;border:1px solid #bbb}
.dots i.on{background:#999}
.content{left:48px;top:545px;width:874px;height:375px;background:linear-gradient(#fff,#f3f3f3)}
.avatar{width:56px;height:66px;border-radius:28px 28px 10px 10px}
.block h2{font-size:15px;font-weight:700;color:#333;margin-bottom:4px}
.block p{font-size:12px;line-height:18.4px;color:#333}
.block.wide p{font-size:12.5px;line-height:22.4px;letter-spacing:.2px}
.block.small p{font-size:11px}
.clients{left:672px;top:566px;width:235px;height:297px;background:linear-gradient(#efefef,#dadada);border:1px solid #ccc}
.clients h3{position:absolute;left:45px;top:22px;font-size:12.5px;font-weight:700;color:#444}
.clients .icon{position:absolute;left:10px;top:14px;width:26px;height:28px}
.clients ul{position:absolute;left:15px;top:52px;list-style:none}
.clients li{font-size:11px;color:#333;height:25.9px;padding-left:17px;position:relative}
.clients li::before{content:"→";position:absolute;left:0;top:-1px;font-size:10px;color:#555}
.features{left:50px;top:922px;width:868px;height:139px;background:var(--panel);border:1px solid #fff}
.feat{top:945px;width:190px}
.feat h4{font-size:13.5px;font-weight:700;color:#333;margin-bottom:14px}
.feat p{font-size:11px;line-height:16.8px;color:#333;padding-left:5px}
.divider{top:934px;width:1px;height:114px;background:#fff;border-left:1px solid #c4c4c4}
.topics{left:48px;top:1062px;width:874px;height:37px;background:linear-gradient(#f3f3f3,#d6d6d6);font-size:13px;font-weight:700;color:#555}
.topics span{position:absolute;top:10px}
.footer{left:48px;top:1099px;width:874px;height:101px;background:var(--footer);color:var(--footer-text);font-size:10.5px;text-align:center}
.footer .links{position:absolute;top:33px;width:100%}
.footer .credit{position:absolute;top:55px;width:100%}
</style>
</head>
<body>
<header class="abs header"></header>
<div class="abs logo">Quill Marsh</div>
<div class="abs social-login"><span class="box"></span>Login</div>
<div class="abs field" style="left:612px;width:110px">User Name</div>
<div class="abs field" style="left:733px;width:110px">Password</div>
<div class="abs btn-login">login</div>
<div class="abs remember"><span></span>Forget Password?</div>

<div class="abs searchbar"></div>
<div class="abs pill" style="left:64px;width:180px">Search</div>
<div class="abs pill topics" style="left:259px;width:115px">Topics</div>
<div class="abs btn-search">SEARCH</div>
<div class="abs adv">ADVANCED SEARCH</div>
<span class="abs social" style="left:754px"></span>
<span class="abs social" style="left:794px"></span>
<span class="abs social" style="left:832px"></span>
<span class="abs social" style="left:870px"></span>

<div class="abs hero" role="img" aria-label="Photo of an advisor in conversation with a client"></div>
<div class="abs caption">"Imagine if, whenever you had a problem you could instantly access the world's experts to solve it. Now you can!"</div>

<nav class="abs menu">
  <a style="left:27px">HOME</a>
  <a style="left:94px">ABOUTS US</a>
  <a style="left:194px">SERVICES</a>
  <a style="left:293px">TESTIMONIALS</a>
  <a style="left:408px">CONTACT US</a>
  <span class="abs dots"><i></i><i class="on"></i><i></i><i></i></span>
</nav>

<section class="abs content"></section>
<div class="abs avatar" style="left:75px;top:574px;background:linear-gradient(#c98a5a 45%,#3b8fd6 45%)" role="img" aria-label="Student figure icon"></div>
<div class="abs block" style="left:157px;top:581px"><h2>Students</h2><p>where you have experience<br>Support &amp; guide people<br>Solve one off issues<br>Provide ongoing mentoring<br>Work when it suits you<br>Pre-book appointments</p></div>
<div class="abs avatar" style="left:378px;top:578px;background:linear-gradient(#6b3a22 45%,#c8242a 45%)" role="img" aria-label="Advisor figure icon"></div>
<div class="abs block wide" style="left:443px;top:582px;width:210px"><h2>Advisors</h2><p>adipiscing elit. Curabitur eu interdum dui. Aliquam turpis mauris, rhoncus et tempus ac, pellentesque quis sem. Nullam a leo arcu, in posuere leo.</p></div>
<div class="abs avatar" style="left:78px;top:754px;background:linear-gradient(#e0a050 45%,#8a5040 45%)" role="img" aria-label="Mentor figure icon with headset"></div>
<div class="abs block small" style="left:152px;top:754px"><h2 style="margin-left:5px">Mentors</h2><p>where you have experience<br>Support &amp; guide people<br>Solve one off issues<br>Provide ongoing mentoring<br>Work when it suits you<br>Pre-book appointments</p></div>
<div class="abs avatar" style="left:368px;top:752px;background:linear-gradient(#2a2a2a 45%,#d42424 45%)" role="img" aria-label="Mentee figure icon with headset"></div>
<div class="abs block small" style="left:442px;top:755px"><h2>Mentees</h2><p>Get online guidance instantly<br>Got a tough issue or need some direction?<br>Shortlist mentors, ask if they can help<br>Get instant results<br>Pay only for the tutor's time you use<br>Need ongoing advice?</p></div>

<aside class="abs clients">
  <svg class="icon" viewBox="0 0 26 28"><circle cx="13" cy="8" r="7" fill="#333"/><path d="M0 28c0-9 6-13 13-13s13 4 13 13z" fill="#333"/></svg>
  <h3>CLIENTS</h3>
  <ul>
    <li>Get online help instantly</li>
    <li>Got a tough question?</li>
    <li>Shortlist advisors, ask them if the know</li>
    <li>Get instant answers to your question</li>
    <li>Pay only for the tutor's time you use</li>
    <li>Need ongoing advice?</li>
    <li>Check advisors resumes</li>
    <li>Choose tutors that meet your budget</li>
    <li>Book appointments when it suits you</li>
  </ul>
</aside>

<section class="abs features"></section>
<span class="abs divider" style="left:253px"></span>
<span class="abs divider" style="left:438px"></span>
<span class="abs divider" style="left:643px"></span>
<div class="abs feat" style="left:72px"><h4>Instant Personal Advice</h4><p>Find advisors<br>waiting online &nbsp;OR<br>Book appointment when it suits</p></div>
<div class="abs feat" style="left:276px"><h4>Direct Video Conference</h4><p>Video in "x" quality<br>Messaging features</p></div>
<div class="abs feat" style="left:471px;width:170px"><h4>Advisors and/or Clients</h4><p>Advisors - Enter your:<br>Topic, buget, availability<br>Clients - SEARCH now<br>Compare ratea, rating &amp; resumes</p></div>
<div class="abs feat" style="left:676px;width:230px"><h4>Paybridge Or Credit Card</h4><p>Charges based on individual advisor's rate<br>Pay only for the time you use<br>Pay via paybridge or credit card<br>Be paid via credit card</p></div>

<div class="abs topics">
  <span style="left:34px">English</span>
  <span style="left:133px">Building</span>
  <span style="left:233px">Cultural Studies</span>
  <span style="left:366px">Criminology</span>
  <span style="left:498px">Agriculture</span>
  <span style="left:598px">Veterinary Science</span>
</div>

<footer class="abs footer">
  <div class="links">Home | Student | Advisors | Topics | Blog | FAQs | Sitemap | About us | Our Technology | Contact</div>
  <div class="credit">Web Designed &amp; Development By Orvello Infotech</div>
</footer>
</body>
</html>
```